BRIGHTHOLD PROPERTY MANAGEMENT INC. WEBSITE

Please make the website more family-friendly.

I want a website to help me build my property management business by adding listing properties and creating an online application. Im open to any other ideas.
I want a WordPress designer to code it.

Here is my current website. www.brighthold.biz

IDEA: I like the website design https://www.pelicanclimateservices.com/

Thank you

Tom

Number of Pages Required

5+ page

```html
<!DOCTYPE html>
<html lang="en">
<head>
<meta charset="utf-8">
<title>Brighthold Property Management</title>
<link href="https://fonts.googleapis.com/css2?family=Cinzel:wght@700&family=Marcellus&family=Playfair+Display:ital,wght@1,700&family=Poppins:wght@400;500;600&display=swap" rel="stylesheet">
<style>
:root{
  --red:#a3141c;
  --red-dark:#6e1015;
  --ink:#111;
  --text:#333;
  --muted:#666;
  --line:#d9d9d9;
  --dark:#2b2b2b;
  --white:#fff;
  --serif:"Marcellus", Georgia, serif;
  --sans:"Poppins", Arial, sans-serif;
}
*{box-sizing:border-box;margin:0;padding:0}
html,body{width:1200px;height:2910px;overflow:hidden;background:var(--white);font-family:var(--sans);color:var(--text)}
.page{position:relative;width:1200px;height:2910px}
.abs{position:absolute}
.lines{white-space:nowrap}

/* header */
.topbar{left:0;top:0;width:1200px;height:82px;background:var(--white)}
.contact-top{right:204px;top:30px;display:flex;gap:32px;font-family:var(--sans);font-weight:500;font-size:17px;color:var(--ink);letter-spacing:.5px}
.contact-top span{display:flex;align-items:center;gap:10px}
.login{right:74px;top:21px;width:100px;height:41px;background:var(--red);color:var(--white);font-family:var(--serif);font-size:15px;letter-spacing:1px;display:flex;align-items:center;justify-content:center;gap:8px}
.navbar{left:0;top:82px;width:1200px;height:59px;background:#000}
.nav{right:74px;top:104px;display:flex;gap:32px;font-family:var(--serif);font-size:14.5px;color:var(--white);letter-spacing:.6px}
.brand-box{left:75px;top:0;width:206px;height:182px;background:var(--white);clip-path:polygon(0 0,100% 0,100% 100%,0 78%)}
.brand{left:75px;top:84px;width:206px;text-align:center;font-family:var(--serif);color:var(--red)}
.brand .mark{display:block;width:40px;height:40px;margin:-60px auto 18px;background:var(--red)}
.brand .name{font-size:27px;letter-spacing:.5px;line-height:1}
.brand .sub{font-size:8px;color:var(--ink);letter-spacing:.6px;margin-top:4px}

/* hero */
.hero{left:0;top:141px;width:1200px;height:593px;background:linear-gradient(180deg,#6e5e88 0%,#8a6f96 30%,#5a5a70 58%,#3e3f4a 75%,#b49a5a 88%,#5a4a32 100%)}
.hero-title{left:0;top:268px;width:1200px;text-align:center;font-family:"Cinzel",serif;font-weight:700;font-size:76px;color:var(--white);letter-spacing:2px}
.hero-sub{left:0;top:350px;width:1200px;text-align:center;font-family:"Playfair Display",serif;font-style:italic;font-weight:700;font-size:32px;color:var(--white)}
.btn{background:var(--red);color:var(--white);font-family:var(--serif);font-size:15px;letter-spacing:1.2px;display:flex;align-items:center;justify-content:center}
.hero-btn{left:524px;top:411px;width:152px;height:45px}
.search{left:253px;top:479px;width:695px;height:50px;background:var(--white);display:flex;align-items:center;justify-content:space-between;padding:0 14px;font-size:14.5px;color:#444}

/* featured */
.section-title{font-family:var(--serif);font-size:33px;color:var(--ink);letter-spacing:.8px}
.featured-title{left:75px;top:798px}
.arrows{right:74px;top:806px;display:flex;gap:12px}
.card{top:873px;width:243px;height:384px;border:1px solid var(--line);background:var(--white);text-align:center}
.card .photo{margin:9px auto 0;width:225px;height:173px}
.card h3{font-family:var(--sans);font-weight:500;font-size:18px;color:var(--ink);margin-top:16px;letter-spacing:.2px;white-space:nowrap}
.card .addr{font-size:12.5px;color:#333;margin-top:4px}
.card .price{font-weight:600;font-size:20px;color:var(--red);margin-top:8px}
.card .meta{display:flex;justify-content:center;align-items:center;gap:10px;font-size:12px;color:#333;margin-top:16px}
.card .meta i{display:inline-block;width:11px;height:9px;border:1.5px solid var(--red);margin-right:4px;vertical-align:-1px}
.card .more{margin:19px auto 0;width:124px;height:37px;background:#111;color:var(--white);font-weight:600;font-size:14.5px;display:flex;align-items:center;justify-content:center}
.ph1{background:linear-gradient(160deg,#9bb8d6,#d8c2a4 55%,#b39a7c)}
.ph2{background:linear-gradient(180deg,#3a7fd0,#a9c7e6 45%,#c9b38e 75%,#6e7f57)}
.ph3{background:linear-gradient(180deg,#e9a25c,#c6785a 40%,#525264 65%,#3c5c2f)}
.ph4{background:linear-gradient(180deg,#c9d9ea,#4a5666 45%,#d8d8d8 78%,#e8e6e2)}

/* about */
.about{left:0;top:1331px;width:1200px;height:507px;background:linear-gradient(110deg,#2a1a1c 0%,#5a1519 35%,#8e1519 65%,#a3141c 100%)}
.about-art{left:680px;top:1390px;width:450px;height:400px;background:radial-gradient(ellipse at center,rgba(255,255,255,.18),rgba(255,255,255,0) 70%)}
.about-title{left:75px;top:1430px;width:560px;font-family:var(--serif);font-size:31px;line-height:40px;color:var(--white);letter-spacing:.6px}
.about-text{left:75px;top:1523px;font-size:14.5px;line-height:27px;color:var(--white)}
.about-btn{left:75px;top:1685px;width:151px;height:46px}

/* services */
.svc-title{left:75px;top:1908px;font-family:var(--serif);font-size:24.5px;line-height:31px;color:var(--ink);letter-spacing:.4px}
.svc-text{left:75px;top:1982px;font-size:15px;line-height:27px;color:#333}
.svc-btn{left:75px;top:2083px;width:151px;height:46px}
.rates{left:793px;top:1912px;width:333px;border-collapse:collapse;font-size:13px}
.rates th{background:#111;color:var(--white);font-family:var(--serif);font-weight:400;font-size:12.5px;letter-spacing:.8px;text-align:left;padding:12px 16px;height:46px;line-height:14px}
.rates td{background:#f4f4f4;padding:0 16px;height:40px;border-top:1px solid #d0d0d0;color:#333}

/* residents */
.res-photo{left:0;top:2196px;width:586px;height:391px;background:linear-gradient(120deg,#e9e7e2 0%,#f7f6f3 40%,#6b4b43 62%,#d9d6cf 80%,#cfcac0 100%)}
.res-panel{left:586px;top:2196px;width:614px;height:391px;background:var(--dark)}
.res-title{left:617px;top:2258px;font-family:var(--serif);font-size:33px;color:var(--white);letter-spacing:.8px}
.res-text{left:617px;top:2310px;font-size:14.5px;line-height:27px;color:var(--white)}
.res-btn{left:617px;top:2470px;width:151px;height:46px}

/* footer */
.f-brand{left:75px;top:2680px;font-family:var(--serif);color:var(--red)}
.f-brand .mark{display:block;width:40px;height:40px;background:var(--red);margin:0 0 18px 52px}
.f-brand .name{font-size:30px;line-height:1}
.f-brand .sub{font-size:9px;color:var(--ink);letter-spacing:.6px;margin-top:2px}
.copy{left:75px;top:2800px;font-size:12px;line-height:23px;color:#555}
.f-head{font-family:var(--serif);font-size:18px;color:var(--red);letter-spacing:.8px;font-weight:400}
.f-links{list-style:none;font-size:13px;line-height:27px;color:#333;margin-top:12px}
.f-contact{font-size:13px;color:#333;margin-top:12px}
.f-contact p{display:flex;gap:12px;line-height:23px;margin-bottom:7px}
.f-contact .ic{width:16px;flex:none;color:var(--red)}
.brk{color:var(--red);font-size:13px}
.badges{display:flex;gap:20px;margin-top:14px}
.badges span{display:block;height:30px;background:#ddd;border:1px solid #999}
.email{width:243px;height:47px;background:#e8e8e8;font-size:13px;color:#444;display:flex;align-items:center;padding-left:15px;margin-top:14px}
.subscribe{width:243px;height:46px;margin-top:9px;background:var(--red);color:var(--white);font-family:var(--serif);font-size:16px;letter-spacing:1px;display:flex;align-items:center;justify-content:center}
.socials{display:flex;gap:17px;margin-top:26px}
.socials span{width:23px;height:23px;border-radius:50%;background:#3a3a3a}
</style>
</head>
<body>
<div class="page">

  <header>
    <div class="abs topbar"></div>
    <div class="abs navbar"></div>
    <div class="abs contact-top">
      <span><svg width="16" height="16" viewBox="0 0 24 24"><path fill="#a3141c" d="M6.6 10.8a15.1 15.1 0 0 0 6.6 6.6l2.2-2.2c.3-.3.7-.4 1-.2 1.1.4 2.3.6 3.6.6.6 0 1 .4 1 1V20c0 .6-.4 1-1 1A17 17 0 0 1 3 4c0-.6.4-1 1-1h3.5c.6 0 1 .4 1 1 0 1.3.2 2.5.6 3.6.1.3 0 .7-.2 1z"/></svg>(916) 555-0142</span>
      <span><svg width="12" height="17" viewBox="0 0 12 18"><rect x="1" y="1" width="10" height="16" rx="1.5" fill="none" stroke="#a3141c" stroke-width="2"/><circle cx="6" cy="14" r="1" fill="#a3141c"/></svg>(916) 555-0142</span>
    </div>
    <div class="abs login btn"><svg width="12" height="14" viewBox="0 0 12 14"><rect x="1" y="6" width="10" height="8" fill="#fff"/><path d="M3 6V4a3 3 0 0 1 6 0v2" fill="none" stroke="#fff" stroke-width="1.8"/></svg>LOGIN</div>
    <nav class="abs nav">
      <span>LISTINGS</span><span>OWNERS</span><span>PROSPECT TENANTS</span><span>ABOUT</span><span>COMMUNITY</span><span>MORTGAGE INFO</span><span>CONTACT</span>
    </nav>
    <div class="abs brand-box"></div>
    <div class="abs brand"><span class="mark"></span><div class="name">BRIGHTHOLD</div><div class="sub">PROPERTY MANAGEMENT &amp; SERVICES</div></div>
  </header>

  <section>
    <div class="abs hero" role="img" aria-label="Modern two-storey house with lit garage doors at dusk"></div>
    <h1 class="abs hero-title">CALL BRIGHTHOLD</h1>
    <p class="abs hero-sub">&amp; Get 1 Month Property Management Fee Off. $120 Value!!</p>
    <div class="abs hero-btn btn">LEARN MORE</div>
    <div class="abs search">Enter address, city, zip
      <svg width="20" height="20" viewBox="0 0 20 20"><circle cx="8" cy="8" r="6" fill="none" stroke="#a3141c" stroke-width="2.6"/><path d="M12.5 12.5l5.5 5.5" stroke="#a3141c" stroke-width="3" stroke-linecap="round"/></svg>
    </div>
  </section>

  <section>
    <h2 class="abs section-title featured-title">FEATURED LISTING</h2>
    <div class="abs arrows">
      <svg width="25" height="25" viewBox="0 0 24 24"><circle cx="12" cy="12" r="12" fill="#111"/><path d="M17 12H8m4-5-5 5 5 5" fill="none" stroke="#fff" stroke-width="2.4"/></svg>
      <svg width="25" height="25" viewBox="0 0 24 24"><circle cx="12" cy="12" r="12" fill="#a3141c"/><path d="M7 12h9m-4-5 5 5-5 5" fill="none" stroke="#fff" stroke-width="2.4"/></svg>
    </div>

    <article class="abs card" style="left:75px">
      <div class="photo ph1" role="img" aria-label="Single-storey rental home beside a large oak tree"></div>
      <h3>1418 Maple Crest Ave</h3><p class="addr">Oakland, CA 94621 Alameda, US</p><p class="price">$2,000.00</p>
      <div class="meta"><span><i></i>693 Sq. Ft.</span><span><i></i>2</span><span><i></i>1</span></div>
      <div class="more">More Info</div>
    </article>
    <article class="abs card" style="left:345px">
      <div class="photo ph2" role="img" aria-label="Low beige ranch house under blue sky"></div>
      <h3>1418 Maple Crest Ave</h3><p class="addr">Oakland, CA 94621 Alameda, US</p><p class="price">$2,000.00</p>
      <div class="meta"><span><i></i>693 Sq. Ft.</span><span><i></i>2</span><span><i></i>1</span></div>
      <div class="more">More Info</div>
    </article>
    <article class="abs card" style="left:616px">
      <div class="photo ph3" role="img" aria-label="Two-storey home at sunset with green lawn"></div>
      <h3>1418 Maple Crest Ave</h3><p class="addr">Oakland, CA 94621 Alameda, US</p><p class="price">$2,000.00</p>
      <div class="meta"><span><i></i>693 Sq. Ft.</span><span><i></i>2</span><span><i></i>1</span></div>
      <div class="more">More Info</div>
    </article>
    <article class="abs card" style="left:884px">
      <div class="photo ph4" role="img" aria-label="Grey craftsman house with white garage doors"></div>
      <h3>1418 Maple Crest Ave</h3><p class="addr">Oakland, CA 94621 Alameda, US</p><p class="price">$2,000.00</p>
      <div class="meta"><span><i></i>693 Sq. Ft.</span><span><i></i>2</span><span><i></i>1</span></div>
      <div class="more">More Info</div>
    </article>
  </section>

  <section>
    <div class="abs about"></div>
    <div class="abs about-art" role="img" aria-label="Soft light glow decoration"></div>
    <h2 class="abs about-title">ABOUT BRIGHTHOLD PROPERTY MANAGEMENT INC</h2>
    <p class="abs about-text lines">Our vision for Brighthold Property Management is to provide the best<br>Property Management Services to the Sacramento and surrounding<br>areas. I am focused on providing a more personalized service to you and<br>your tenants. This means we are a one-stop-shop. You only deal with<br>me, no middle guy, so no time is wasted.</p>
    <div class="abs about-btn btn">LEARN MORE</div>
  </section>

  <section>
    <h2 class="abs svc-title lines">PROPERTY MANAGEMENT ELK GROVE, SACRAMENTO<br>&amp; SURROUNDING AREAS</h2>
    <p class="abs svc-text lines">Having the right property manager means having an agent who is committed to helping<br>you and making being a home provider hassle free. I believe clear communication, work<br>ethic, time management, staying focused and knowledge goes a long way in my business.</p>
    <div class="abs svc-btn btn">LEARN MORE</div>
    <table class="abs rates">
      <tr><th>NATIONAL</th><th style="width:100px">AVERAGE RATE*</th></tr>
      <tr><td>30-Year FHA Rate</td><td>7.07%</td></tr>
      <tr><td>30-Year Fixed Rate</td><td>5.88%</td></tr>
      <tr><td>20-Year Fixed Rate</td><td>7.19%</td></tr>
      <tr><td>15-Year Fixed Rate</td><td>6.61%</td></tr>
    </table>
  </section>

  <section>
    <div class="abs res-photo" role="img" aria-label="Happy family arriving in their bright new home"></div>
    <div class="abs res-panel"></div>
    <h2 class="abs res-title">FOR RESIDENTS</h2>
    <p class="abs res-text lines">We know you have a choice in places to live and we sincerely<br>appreciate your choice to live in one of our managed homes.<br>We want you to enjoy a hassle free experience so if you have any<br>questions or need any assistance, please call immediately<br>at 916-555-0142.</p>
    <div class="abs res-btn btn">LEARN MORE</div>
  </section>

  <footer>
    <div class="abs f-brand"><span class="mark"></span><div class="name">BRIGHTHOLD</div><div class="sub">PROPERTY MANAGEMENT &amp; SERVICES</div></div>
    <p class="abs copy">© Copyright 2024 Company Name<br>All Rights Reserved.</p>

    <div class="abs" style="left:368px;top:2638px">
      <h4 class="f-head">QUICK LINKS</h4>
      <ul class="f-links"><li>Listings</li><li>Owners</li><li>Prospect Tenants</li><li>About</li><li>Community</li><li>Mortgage Info</li></ul>
    </div>

    <div class="abs" style="left:597px;top:2638px">
      <h4 class="f-head">CONTACT INFO</h4>
      <div class="f-contact">
        <p><span class="ic"><svg width="15" height="12" viewBox="0 0 16 13"><path d="M0 2l5-2 6 2 5-2v11l-5 2-6-2-5 2z" fill="#a3141c"/></svg></span><span>4480 Larkspur Way #210<br>Sacramento , CA 95822</span></p>
        <p><span class="ic"><svg width="13" height="13" viewBox="0 0 24 24"><path fill="#a3141c" d="M6.6 10.8a15.1 15.1 0 0 0 6.6 6.6l2.2-2.2c.3-.3.7-.4 1-.2 1.1.4 2.3.6 3.6.6.6 0 1 .4 1 1V20c0 .6-.4 1-1 1A17 17 0 0 1 3 4c0-.6.4-1 1-1h3.5c.6 0 1 .4 1 1 0 1.3.2 2.5.6 3.6.1.3 0 .7-.2 1z"/></svg></span><span>(916) 555-0142</span></p>
        <p><span class="ic"><svg width="9" height="13" viewBox="0 0 12 18"><rect x="1" y="1" width="10" height="16" rx="1.5" fill="none" stroke="#a3141c" stroke-width="2"/></svg></span><span>(916) 555-0142</span></p>
        <p class="brk">BRK# 02945518</p>
      </div>
      <div class="badges"><span style="width:24px"></span><span style="width:58px"></span><span style="width:24px"></span></div>
    </div>

    <div class="abs" style="left:884px;top:2638px">
      <h4 class="f-head">NEWSLETTER</h4>
      <div class="email">Email Address</div>
      <div class="subscribe">SUBSCRIBE</div>
      <div class="socials"><span></span><span></span><span></span><span></span><span></span></div>
    </div>
  </footer>

</div>
</body>
</html>
```